Business Card Design - ChoiceCraft

Looking for creative, modern design, two sided for ChoiceCraft that is consistent with color and feel of website www.choicecraftpro.net.
Updates

Back of card will be used to promote products or have a quote revolving around decisions, change, leadership, innovation, creativity. Back should also have space to promote website, but optional to use the icon. Front of the card will need to use the icon and have standard place for name, job title, phone and email. We are not looking to put a mailing address or fax. Also want space to place a few words/phrase explaining what we do...such as individual growth and organizational development or tools, training, information...in addition, want the facebook icon small on the front somewhere as we are also on facebook.

Vector file uploaded of icon.

Target Market(s)

Professional coaching for individual growth and organizational development

Industry/Entity Type

Business

Requirements
Must have
• Icon...see attached.

```html
<!DOCTYPE html>
<html lang="en">
<head>
<meta charset="utf-8">
<title>ChoiceCraft Business Card</title>
<link rel="stylesheet" href="https://fonts.googleapis.com/css2?family=Open+Sans:wght@400;600;700&display=swap">
<style>
  :root {
    --page-bg: #e9ecef;
    --card-white: #ffffff;
    --band-light: #35c1ef;
    --band-dark: #1688cf;
    --back-center: #45cdf7;
    --back-edge: #0a66b8;
    --ink-dark: #1b1b1b;
    --ink-grey: #444b52;
    --ink-white: #ffffff;
    --mark-blue: #1f8fd6;
    --mark-silver: #b9bec4;
    --shadow: rgba(0, 0, 0, 0.25);
  }
  * { box-sizing: border-box; margin: 0; padding: 0; }
  html, body {
    width: 1200px; height: 763px; overflow: hidden;
    background: var(--page-bg);
    font-family: "Open Sans", Arial, sans-serif;
  }
  .stage {
    width: 1200px; height: 763px;
    display: flex; align-items: center; justify-content: center; gap: 40px;
  }
  .card {
    width: 550px; height: 320px; border-radius: 18px; overflow: hidden;
    position: relative; box-shadow: 0 10px 28px var(--shadow);
  }

  /* Front */
  .card-front { background: var(--card-white); display: flex; flex-direction: column; }
  .front-brand {
    height: 150px; display: flex; align-items: center; padding-left: 118px; gap: 16px;
  }
  .brand-dot {
    width: 78px; height: 78px; border-radius: 50%; background: var(--mark-blue); flex: none;
  }
  .brand-name { font-size: 30px; font-weight: 400; color: var(--ink-dark); letter-spacing: 0.2px; }
  .front-band {
    height: 118px;
    background: linear-gradient(180deg, var(--band-light) 0%, var(--band-light) 30%, var(--band-dark) 100%);
    display: flex; align-items: center; justify-content: center; gap: 18px; padding-left: 40px;
  }
  .person { text-align: right; color: var(--ink-white); padding-top: 30px; }
  .person-name { font-size: 22px; font-weight: 700; line-height: 1.1; }
  .person-title { font-size: 16px; font-weight: 400; }
  .divider { width: 1px; height: 78px; background: rgba(255,255,255,0.7); }
  .contacts { list-style: none; color: var(--ink-white); font-size: 14.5px; line-height: 1.42; }
  .contacts li { display: flex; align-items: center; gap: 6px; }
  .contacts svg { width: 11px; height: 11px; flex: none; }
  .social-square { width: 10px; height: 10px; background: var(--ink-white); flex: none; }
  .front-tagline {
    flex: 1; display: flex; align-items: center; justify-content: center;
    border-top: 4px solid var(--card-white);
    background: linear-gradient(180deg, #f4f6f8, #ffffff);
    color: var(--ink-grey); font-size: 14px;
  }

  /* Back */
  .card-back {
    background: radial-gradient(ellipse 60% 70% at 48% 38%, var(--back-center) 0%, #1d96dd 50%, var(--back-edge) 100%);
    color: var(--ink-white); padding: 26px 0 0 40px;
  }
  .quotes { list-style: none; }
  .quote { margin-bottom: 6px; }
  .quote-text { font-size: 14.5px; line-height: 1.3; }
  .quote-text::before { content: "\201C"; font-weight: 700; font-size: 20px; margin-right: 2px; vertical-align: -3px; }
  .quote-text::after { content: "\201D"; font-weight: 700; font-size: 20px; margin-left: 2px; vertical-align: -9px; }
  .quote-author { font-size: 14px; font-weight: 700; padding-left: 16px; line-height: 1.2; }
  .back-mark {
    position: absolute; right: 40px; bottom: 30px; width: 96px; height: 96px; border-radius: 50%;
    background: var(--mark-silver);
  }
</style>
</head>
<body>
<main class="stage">
  <section class="card card-front" aria-label="Card front">
    <div class="front-brand">
      <span class="brand-dot" aria-hidden="true"></span>
      <span class="brand-name">ChoiceCraft</span>
    </div>
    <div class="front-band">
      <div class="person">
        <div class="person-name">Your Name</div>
        <div class="person-title">Title</div>
      </div>
      <span class="divider" aria-hidden="true"></span>
      <ul class="contacts">
        <li>
          <svg viewBox="0 0 12 12" aria-hidden="true"><path d="M2.5 1h2l1 3-1.4 1a6 6 0 0 0 2.9 2.9L8 6.5l3 1v2c0 .8-.7 1.5-1.5 1.5A8.5 8.5 0 0 1 1 2.5C1 1.7 1.7 1 2.5 1z" fill="#fff"/></svg>
          123-456-789
        </li>
        <li>
          <svg viewBox="0 0 12 12" aria-hidden="true"><rect x="0.5" y="2" width="11" height="8" rx="1" fill="#fff"/><path d="M1 2.5l5 4 5-4" stroke="#1b8fd3" stroke-width="1.1" fill="none"/></svg>
          info@choicecraftpro.net
        </li>
        <li>
          <svg viewBox="0 0 12 12" aria-hidden="true"><circle cx="6" cy="6" r="5" fill="none" stroke="#fff" stroke-width="1.2"/><ellipse cx="6" cy="6" rx="2.2" ry="5" fill="none" stroke="#fff" stroke-width="1"/><path d="M1 6h10" stroke="#fff" stroke-width="1"/></svg>
          www.choicecraftpro.net
        </li>
        <li>
          <span class="social-square" aria-hidden="true"></span>
          /choicecraftpro
        </li>
      </ul>
    </div>
    <div class="front-tagline">Supporting individual growth and organizational development.</div>
  </section>

  <section class="card card-back" aria-label="Card back">
    <ul class="quotes">
      <li class="quote">
        <p class="quote-text">Try not to become a man of success, but rather a man of value.</p>
        <p class="quote-author">- Alden Ashby</p>
      </li>
      <li class="quote">
        <p class="quote-text">The only constant is change.</p>
        <p class="quote-author">- Helio Varro</p>
      </li>
      <li class="quote">
        <p class="quote-text">We are what we repeatedly do. Excellence is not an act, it is a habit.</p>
        <p class="quote-author">- Arion Thale</p>
      </li>
      <li class="quote">
        <p class="quote-text">Simplicity is the ultimate sophistication.</p>
        <p class="quote-author">- Lorenzo Vale</p>
      </li>
      <li class="quote">
        <p class="quote-text">Life is not fair - get used to it.</p>
        <p class="quote-author">- Bram Gilles</p>
      </li>
    </ul>
    <span class="back-mark" aria-hidden="true"></span>
  </section>
</main>
</body>
</html>
```